PLW Gourmet Fungi web presence and site

The goal is to attract local buyers of fresh mushrooms and to both local and international buyers freeze dried mushrooms. Mushrooms grown will be oyster mushrooms (yellow, pink, blue, king), shiitake, lions main, chestnut, and more. My business will also be selling grow kits that help families who would like to grow there own mushrooms

Target Market(s)

Local restaurants, foodies and people seeking high quality fresh and freeze dried gourmet mushrooms

Font styles to use
Serif

Requirements
Must have
• Pictures of the various mushrooms grown along with the characteristics of each of the mushrooms. Recipes and cooking tips for the various mushrooms. There needs to be
1. Order forms with online payments
2. Feedback
3. Preorders for mushrooms that may be more seasonal
4.links to social media Facebook, LinkedIn, etc... I am not knowledgeable in this area
5. Contact Us link email, address, phone
6. About Us link explaining Mark Oduya & Sonia Pettimore and a brief explanation about us and why we became Mushroom farmers
7. Descriptions of the various mushroom varieties grown and how they are best prepared and served
8. Why Freeze Drying mushrooms and the benefits of Freeze Drying over other methods of preservation.
Nice to have
• 1. Recipes and cooking tips for each of the mushrooms.
2. Weekly additional resources added to different pages
3. Q&A section
4. Food Blog with resources added weekly
5.

Flexibility with future expansion and growth is essential. I would like to have a growing site, not a stagnant site.
Should not have
• 1. Boring, bland presentation.
2. The web site is one to educate, promote the various mushrooms grown
3. No music, video or sound on the main pages but eventually a Vlog might be in the works.

I realize there is a lot of content requested but the content needs to attract buyers and to have the site a go to site for foodies

```html
<!DOCTYPE html>
<html lang="en">
<head>
<meta charset="utf-8">
<title>PLW Gourmet Fungi</title>
<link href="https://fonts.googleapis.com/css2?family=Montserrat:wght@300;400;500;600;700;800&family=Roboto:ital,wght@0,300;0,400;0,500;0,700;1,400&display=swap" rel="stylesheet">
<style>
:root{
  --orange:#f7a11a;
  --orange-deep:#e0780f;
  --ink:#222;
  --text:#555;
  --muted:#777;
  --light:#f2f2f2;
  --dark-brown:#2b1a17;
  --btn-brown:#3a2412;
  --white:#fff;
}
*{margin:0;padding:0;box-sizing:border-box}
html,body{width:1200px;height:5155px;overflow:hidden}
body{font-family:'Roboto',sans-serif;color:var(--text);background:var(--white);position:relative}
h1,h2,h3,h4{font-weight:400}
.section{position:absolute;left:0;width:1200px;overflow:hidden}
.abs{position:absolute}
.heading{font-family:'Montserrat',sans-serif;font-weight:400;color:var(--ink);letter-spacing:1px;font-size:28px;text-align:center;width:100%}
.heading b{font-weight:700}
.btn{position:absolute;display:flex;align-items:center;justify-content:center;border-radius:30px;font-family:'Montserrat',sans-serif;font-weight:600;font-size:16px;color:var(--white);background:var(--orange)}

/* header */
.site-header{top:0;height:104px;background:var(--white)}
.wordmark{left:96px;top:38px;font-family:'Montserrat',sans-serif;font-size:22px;font-weight:600;color:#333;letter-spacing:.5px;white-space:nowrap}
.main-nav{left:388px;top:40px;display:flex;font-family:'Montserrat',sans-serif;font-size:13px;font-weight:600;color:#888}
.main-nav span{margin-right:32px;position:relative}
.main-nav .active{color:#222}
.main-nav .active:after{content:"";position:absolute;left:20px;right:20px;bottom:-10px;height:2px;background:var(--orange)}

/* hero */
.hero{top:104px;height:632px}
.hero-photo{position:absolute;inset:0;background:linear-gradient(100deg,#1e1e1e 0%,#2a2522 30%,#5a3e2a 55%,#7a5535 72%,#4a3322 100%)}
.hero-welcome{left:116px;top:198px;font-family:'Montserrat',sans-serif;font-size:32px;font-weight:400;color:var(--white);letter-spacing:1px}
.hero-title{left:116px;top:234px;font-family:'Montserrat',sans-serif;font-size:46px;font-weight:700;color:var(--white);line-height:48px;letter-spacing:1px}
.hero .btn{left:110px;top:352px;width:268px;height:56px;font-size:17px}
.hero-dots{left:1124px;top:250px}
.hero-dots i{display:block;width:14px;height:14px;border-radius:50%;background:var(--white);margin-bottom:10px}

/* about */
.about{top:736px;height:544px;background:var(--light)}
.about-photo-main{left:140px;top:72px;width:376px;height:392px;background:linear-gradient(160deg,#8fa07a,#4b5a3a 50%,#6a4a3a);box-shadow:0 4px 10px rgba(0,0,0,.2)}
.about-photo-small{left:392px;top:270px;width:204px;height:212px;background:var(--white);padding:8px;box-shadow:0 4px 12px rgba(0,0,0,.25)}
.about-photo-small div{width:100%;height:100%;background:linear-gradient(135deg,#8a5a2e,#c89a62 50%,#6b4422)}
.about-kicker{left:634px;top:102px;font-family:'Montserrat',sans-serif;font-size:24px;color:var(--ink);letter-spacing:1px}
.about-names{left:634px;top:130px;font-family:'Montserrat',sans-serif;font-size:30px;font-weight:700;color:var(--ink);line-height:34px;letter-spacing:.5px}
.about-copy{left:634px;top:218px;width:500px;font-size:13.5px;line-height:27px;color:#444}
.about-copy p{margin-bottom:14px}
.about .btn{left:632px;top:386px;width:178px;height:50px;font-size:15px}

/* varieties */
.varieties{top:1280px;height:524px}
.varieties .heading{top:66px}
.variety{position:absolute;top:138px;width:260px;text-align:center}
.variety .pic{width:220px;height:220px;border-radius:50%;margin:0 auto;background:radial-gradient(circle at 45% 40%,#b98a5e,#6e4526 60%,#3a2514)}
.variety h3{font-size:16px;font-weight:500;color:#222;margin-top:18px}
.variety p{font-size:13.5px;line-height:20px;color:#666;margin-top:6px}
.arrow{position:absolute}

/* why freeze */
.why{top:1804px;height:544px;background:linear-gradient(90deg,var(--orange-deep) 0%,#ef8c12 50%,var(--orange) 100%)}
.why-kicker{left:122px;top:100px;font-family:'Montserrat',sans-serif;font-size:30px;color:var(--white);letter-spacing:1px}
.why-title{left:122px;top:132px;font-family:'Montserrat',sans-serif;font-size:30px;font-weight:700;color:var(--white);letter-spacing:1px}
.why-copy{left:122px;top:190px;width:470px;font-size:13.5px;line-height:26px;color:var(--white)}
.why-copy p{margin-bottom:10px}
.why .btn{left:120px;top:386px;width:200px;height:56px;background:var(--btn-brown);font-size:17px}
.why-photo{left:660px;top:104px;width:320px;height:320px;transform:rotate(12deg);background:radial-gradient(circle,#6a4a30 0%,#a77c4c 45%,#caa06a 70%,#a0784a 100%);box-shadow:0 14px 30px rgba(0,0,0,.35)}

/* benefits */
.benefits{top:2348px;height:562px}
.benefits .heading{top:72px}
.benefit{position:absolute;width:400px}
.benefit h4{font-size:17px;font-weight:400;color:#333}
.benefit p{font-size:13.5px;color:#777;margin-top:8px}
.benefit.left{text-align:right}
.benefit svg{position:absolute;top:-2px}
.benefit.left svg{right:-36px}
.benefit.right svg{left:-36px}
.benefit-photo{left:462px;top:220px;width:280px;height:196px;border-radius:50% 50% 40% 40%;background:radial-gradient(ellipse at 40% 40%,#d9b48a,#a8784c 60%,#e8dccc 100%)}

/* recipes */
.recipes{top:2910px;height:582px;background:var(--dark-brown)}
.recipes .heading{top:56px;color:var(--white)}
.recipe{position:absolute;top:132px;width:316px;height:356px;background:var(--white)}
.recipe .pic{height:214px}
.recipe .body{padding:20px 32px}
.recipe h3{font-size:17px;font-weight:500;color:#222}
.recipe p{font-size:13px;line-height:20px;color:#666;margin-top:8px}
.recipe a{display:block;font-size:13px;font-weight:700;color:var(--orange);margin-top:4px;text-decoration:none}

/* reviews */
.reviews{top:3492px;height:434px;background:#efefef}
.reviews .heading{top:70px}
.review-photo{left:242px;top:108px;width:200px;height:200px;border-radius:50%;background:linear-gradient(160deg,#8fa868,#5b6e3a 60%,#7a4a5a)}
.review-quote{left:470px;top:150px;width:540px;font-style:italic;font-size:19px;line-height:34px;color:#555}
.review-author{left:470px;top:272px;font-size:19px;font-weight:700;color:#222}
.review-stars{left:468px;top:312px;display:flex;gap:4px}

/* Q&A */
.qa{top:3926px;height:550px}
.qa-photo{left:60px;top:96px;width:510px;height:320px;border-radius:45% 55% 40% 50%;background:radial-gradient(ellipse at 50% 50%,#b17a4e,#8a5532 50%,#f5eee6 75%,#fff 100%)}
.qa-title{left:626px;top:92px;font-family:'Montserrat',sans-serif;font-size:28px;font-weight:400;color:var(--ink);letter-spacing:1px}
.qa-title b{font-weight:700}
.qa-list{left:626px;top:158px;width:540px}
.qa-item{position:relative;padding-left:24px;font-size:16px;color:#444;margin-bottom:26px}
.qa-item:before{content:"+";position:absolute;left:0;top:-3px;color:var(--orange);font-size:22px;font-weight:400}
.qa-item.open:before{content:"-";color:#444;font-size:18px;top:-2px}
.qa-item .answer{font-size:13.5px;line-height:24px;color:#666;margin-top:10px}

/* contact */
.contact{top:4476px;height:528px}
.contact-left{position:absolute;left:0;top:0;width:576px;height:528px;background:linear-gradient(160deg,#3a3330,#2a2422)}
.contact-right{position:absolute;left:576px;top:0;width:624px;height:528px;background:linear-gradient(150deg,#f29a20,#e8821a 50%,#d46a10)}
.contact-title{left:118px;top:76px;font-family:'Montserrat',sans-serif;font-size:28px;font-weight:400;color:var(--white);letter-spacing:1px}
.contact-title b{font-weight:700}
.contact-item{position:absolute;left:118px;color:var(--white);font-size:15px;line-height:22px;padding-left:40px}
.contact-item svg{position:absolute;left:0;top:4px}
.socials{left:118px;top:342px;display:flex;gap:6px}
.socials i{display:block;width:38px;height:38px;border-radius:50%;border:2px solid var(--white)}
.order-title{left:646px;top:76px;font-family:'Montserrat',sans-serif;font-size:28px;font-weight:400;color:var(--white);letter-spacing:1px}
.order-title b{font-weight:700}
.field{position:absolute;width:238px;height:44px;border:1px solid rgba(255,255,255,.75);color:var(--white);font-size:14px;padding:12px 18px}
.field.message{width:486px;height:86px}
.submit{position:absolute;left:654px;top:402px;width:176px;height:54px;background:var(--btn-brown);color:var(--white);font-weight:700;font-size:15px;display:flex;align-items:center;justify-content:center}
.cards{left:890px;top:420px;display:flex;gap:8px}
.cards span{display:flex;align-items:center;justify-content:center;width:38px;height:20px;background:var(--white);border-radius:2px;font-size:8px;font-weight:700;color:#555}

/* footer */
.site-footer{top:5004px;height:151px}
.footer-nav{position:absolute;left:0;top:48px;width:100%;display:flex;justify-content:center;gap:32px;font-family:'Montserrat',sans-serif;font-size:13px;font-weight:700;color:#222}
.copyright{position:absolute;top:90px;width:100%;text-align:center;font-size:13px;color:#555}
</style>
</head>
<body>

<header class="section site-header">
  <div class="abs wordmark">PLW Gourmet Fungi</div>
  <nav class="abs main-nav">
    <span class="active">ABOUT US</span><span>WHY US</span><span>OUR MASHROOMS</span><span>RECIEPE</span><span>REVIEWS</span><span>BLOGS</span><span>Q&amp;A</span><span>CONTACT</span>
  </nav>
</header>

<section class="section hero">
  <div class="hero-photo" role="img" aria-label="Fresh brown mushrooms with herbs on a dark wooden table"></div>
  <div class="abs hero-welcome">WELCOME TO</div>
  <h1 class="abs hero-title">PLW GOURMET<br>FUNGI</h1>
  <div class="btn">SEASONAL PREORDER</div>
  <div class="abs hero-dots"><i></i><i></i><i></i></div>
</section>

<section class="section about">
  <div class="abs about-photo-main" role="img" aria-label="The two growers standing in a field holding a crate of produce"></div>
  <div class="abs about-photo-small"><div role="img" aria-label="Wooden crate filled with small mushrooms"></div></div>
  <div class="abs about-kicker">ABOUT US</div>
  <h2 class="abs about-names">MARK ODUYA &amp;<br>SONIA PETTIMORE</h2>
  <div class="abs about-copy">
    <p>lectus feugiat felis Morbi diam mauris viverra in gravida eu mattis in ante Morbi eget arcu Morbi porta libero id ullamcorper nonummy</p>
    <p>Ut ac mi quis lacus mollis aliquam Curabitur iaculis tempus eros Curabitur vel mi sit amet magna malesuada ultrices Ut nisi erat fermentum vel congue id euismod in elit Fusce ultricies orci ac feugiat suscipit le</p>
  </div>
  <div class="btn">LEARN MORE</div>
</section>

<section class="section varieties">
  <h2 class="abs heading"><b>MUSHROOMS</b> VARITIES</h2>
  <svg class="arrow" style="left:58px;top:224px" width="24" height="40" viewBox="0 0 24 40"><path d="M20 3 4 20l16 17" fill="none" stroke="#aaa" stroke-width="3"/></svg>
  <svg class="arrow" style="left:1122px;top:224px" width="24" height="40" viewBox="0 0 24 40"><path d="M4 3l16 17L4 37" fill="none" stroke="#aaa" stroke-width="3"/></svg>
  <div class="variety" style="left:84px"><div class="pic" role="img" aria-label="Pile of dried shiitake mushrooms"></div><h3>Mashroom Title</h3><p>Augiat in pede Fusce tellus Sed<br>metus augue convallis</p></div>
  <div class="variety" style="left:342px"><div class="pic" role="img" aria-label="Red capped mushroom in moss" style="background:radial-gradient(circle at 45% 40%,#c0392b,#6e2a1a 55%,#2a2a20)"></div><h3>Mashroom Title</h3><p>Augiat in pede Fusce tellus Sed<br>metus augue convallis</p></div>
  <div class="variety" style="left:606px"><div class="pic" role="img" aria-label="Two brown shiitake mushrooms on grey stone" style="background:radial-gradient(circle at 45% 50%,#7a4a2a,#5a5a5a 60%,#3a3a3a)"></div><h3>Mashroom Title</h3><p>Augiat in pede Fusce tellus Sed<br>metus augue convallis</p></div>
  <div class="variety" style="left:864px"><div class="pic" role="img" aria-label="Cluster of light brown mushrooms" style="background:radial-gradient(circle at 45% 40%,#d8b898,#9a6a44 60%,#5a3a24)"></div><h3>Mashroom Title</h3><p>Augiat in pede Fusce tellus Sed<br>metus augue convallis</p></div>
</section>

<section class="section why">
  <div class="abs why-kicker">WHY FREEZE</div>
  <h2 class="abs why-title">DRYING MUSHROOMS</h2>
  <div class="abs why-copy">
    <p>Augiat in pede Fusce tellus Sed metus augue convallis et vehicula ut pulvinar eu ante Integer orci tellus tristique vitae consequat</p>
    <p>Morbi eget arcurmentum vel congue id euismod in elit Fusce ultricies orci ac feugiat suscipit leo massa sodales velit et scelerisque mi tortor at ipsum Proin orci odio commodo ac gravida non tristique vel te Curabitur iaculis tempus eros Curabitur vel mi</p>
  </div>
  <div class="btn">LEARN MORE</div>
  <div class="abs why-photo" role="img" aria-label="Wooden bowl of shiitake mushrooms on a woven mat"></div>
</section>

<section class="section benefits">
  <h2 class="abs heading">BENEFITS <b>OF FREEZE DRYING</b></h2>
  <svg width="0" height="0" style="position:absolute"><defs><g id="tick"><circle cx="15" cy="15" r="13" fill="none" stroke="#f7a11a" stroke-width="2"/><path d="M9 15l4 4 8-9" fill="none" stroke="#f7a11a" stroke-width="2"/></g></defs></svg>
  <div class="benefit left" style="left:60px;top:168px"><h4>Praesent sit amet est In</h4><p>dictum dolor eu dictum porttitor enim felis</p><svg width="30" height="30"><use href="#tick"/></svg></div>
  <div class="benefit left" style="left:0;top:298px"><h4>Curabitur iaculis tempus</h4><p>dictum dolor eu dictum porttitor enim felis</p><svg width="30" height="30"><use href="#tick"/></svg></div>
  <div class="benefit left" style="left:60px;top:432px"><h4>Curabitur iaculis tempus</h4><p>dictum dolor eu dictum porttitor enim felis</p><svg width="30" height="30"><use href="#tick"/></svg></div>
  <div class="benefit right" style="left:762px;top:168px"><h4>Praesent sit amet est In</h4><p>dictum dolor eu dictum porttitor enim felis</p><svg width="30" height="30"><use href="#tick"/></svg></div>
  <div class="benefit right" style="left:824px;top:298px"><h4>Curabitur iaculis tempus</h4><p>dictum dolor eu dictum porttitor enim felis</p><svg width="30" height="30"><use href="#tick"/></svg></div>
  <div class="benefit right" style="left:762px;top:432px"><h4>Curabitur iaculis tempus</h4><p>dictum dolor eu dictum porttitor enim felis</p><svg width="30" height="30"><use href="#tick"/></svg></div>
  <div class="abs benefit-photo" role="img" aria-label="Two whole brown mushrooms"></div>
</section>

<section class="section recipes">
  <h2 class="abs heading">RECIPES AND <b>COOKING TIPS</b></h2>
  <article class="recipe" style="left:100px"><div class="pic" role="img" aria-label="Plate of roasted mushrooms with greens" style="background:linear-gradient(135deg,#6a8a3a,#b8742e 50%,#e8e0d4)"></div><div class="body"><h3>Recipe Title here</h3><p>Lorem ipsum dolor sit amet consect etuer adipiscing elit Nam cursus</p><a>LEARN MORE</a></div></article>
  <article class="recipe" style="left:446px"><div class="pic" role="img" aria-label="Baking dish of roasted chicken with mushrooms" style="background:linear-gradient(135deg,#3a3a3a,#a8702a 50%,#5a4a3a)"></div><div class="body"><h3>Recipe Title here</h3><p>Lorem ipsum dolor sit amet consect etuer adipiscing elit Nam cursus</p><a>LEARN MORE</a></div></article>
  <article class="recipe" style="left:792px"><div class="pic" role="img" aria-label="Pan of sautéed mushrooms on dark slate" style="background:linear-gradient(135deg,#2e2e2e,#6a4a2e 55%,#3a3a3a)"></div><div class="body"><h3>Recipe Title here</h3><p>Lorem ipsum dolor sit amet consect etuer adipiscing elit Nam cursus</p><a>LEARN MORE</a></div></article>
</section>

<section class="section reviews">
  <h2 class="abs heading">REVIEWS &amp; <b>FEEDBACK</b></h2>
  <svg class="arrow" style="left:112px;top:192px" width="24" height="40" viewBox="0 0 24 40"><path d="M20 3 4 20l16 17" fill="none" stroke="#999" stroke-width="3"/></svg>
  <svg class="arrow" style="left:1068px;top:192px" width="24" height="40" viewBox="0 0 24 40"><path d="M4 3l16 17L4 37" fill="none" stroke="#999" stroke-width="3"/></svg>
  <div class="abs review-photo" role="img" aria-label="Portrait of a smiling customer in a field"></div>
  <blockquote class="abs review-quote">Morbi diam mauris viverra in gravida eu mattis in anquam<br>Cura bitur vel dolor ultrices ipsum dictum tristique Prae<br>sent vitae lacus Ut velit enim vestibulum non</blockquote>
  <div class="abs review-author">By Author Name</div>
  <div class="abs review-stars">
    <svg width="24" height="24" viewBox="0 0 24 24"><path d="M12 2l3 6.5 7 .8-5.2 4.8 1.4 7L12 17.6 5.8 21l1.4-7L2 9.3l7-.8z" fill="#f7a11a"/></svg>
    <svg width="24" height="24" viewBox="0 0 24 24"><path d="M12 2l3 6.5 7 .8-5.2 4.8 1.4 7L12 17.6 5.8 21l1.4-7L2 9.3l7-.8z" fill="#f7a11a"/></svg>
    <svg width="24" height="24" viewBox="0 0 24 24"><path d="M12 2l3 6.5 7 .8-5.2 4.8 1.4 7L12 17.6 5.8 21l1.4-7L2 9.3l7-.8z" fill="#f7a11a"/></svg>
    <svg width="24" height="24" viewBox="0 0 24 24"><path d="M12 2l3 6.5 7 .8-5.2 4.8 1.4 7L12 17.6 5.8 21l1.4-7L2 9.3l7-.8z" fill="#f7a11a"/></svg>
    <svg width="24" height="24" viewBox="0 0 24 24"><path d="M12 2l3 6.5 7 .8-5.2 4.8 1.4 7L12 17.6 5.8 21l1.4-7L2 9.3l7-.8z" fill="#f7a11a"/></svg>
  </div>
</section>

<section class="section qa">
  <div class="abs qa-photo" role="img" aria-label="Group of brown mushrooms with a sprig of rosemary"></div>
  <h2 class="abs qa-title">QUESTION &amp; <b>ANSWER</b></h2>
  <div class="abs qa-list">
    <div class="qa-item open">Morbi diam mauris viverra in gravida eu mattis in anquam
      <div class="answer">Ael tellus Pellentesque nibh libero ultricies eu sagittis non mollis sed justo Praesent metus ipsum pulvinar pulvinar porta id fringilla at est Phasellus felis dolor scelerisque a tempus eget lobortis id libero</div></div>
    <div class="qa-item">Curabitur vel dolor ultrices ipsum dictum</div>
    <div class="qa-item">Praesent vitae lacus Ut velit enim vestibulum non</div>
    <div class="qa-item">Aliquam nec erat at purus cursus interdum</div>
    <div class="qa-item">Vestibulum ligula augue bibendum</div>
  </div>
</section>

<section class="section contact">
  <div class="contact-left" role="img" aria-label="Dark toned photo of mushrooms behind the contact details"></div>
  <div class="contact-right" role="img" aria-label="Orange toned photo of mushrooms behind the order form"></div>
  <h2 class="abs contact-title">CONTACT <b>US</b></h2>
  <div class="contact-item" style="top:136px"><svg width="20" height="24" viewBox="0 0 20 24"><path d="M10 1a8 8 0 0 0-8 8c0 6 8 14 8 14s8-8 8-14a8 8 0 0 0-8-8zm0 11a3 3 0 1 1 0-6 3 3 0 0 1 0 6z" fill="#fff"/></svg>Address<br>48 Meadow Lane #4B Austin TX 73301</div>
  <div class="contact-item" style="top:206px"><svg width="20" height="20" viewBox="0 0 20 20"><path d="M4 2l3 0 2 4-2 2a11 11 0 0 0 5 5l2-2 4 2v3a2 2 0 0 1-2 2A16 16 0 0 1 2 4a2 2 0 0 1 2-2z" fill="none" stroke="#fff" stroke-width="1.8"/></svg>Phone Number<br>(555) 014 2287</div>
  <div class="contact-item" style="top:276px"><svg width="20" height="16" viewBox="0 0 20 16"><rect x="1" y="1" width="18" height="14" fill="#fff"/><path d="M1 1l9 8 9-8" fill="none" stroke="#2f2a27" stroke-width="1.6"/></svg>Email address<br>hello@plwfungi.com</div>
  <div class="abs socials" aria-label="Social media links"><i></i><i></i><i></i><i></i></div>

  <h2 class="abs order-title">ORDER <b>NOW</b></h2>
  <div class="field" style="left:652px;top:136px">First Name</div>
  <div class="field" style="left:900px;top:136px">Last Name</div>
  <div class="field" style="left:652px;top:192px">Email address</div>
  <div class="field" style="left:900px;top:192px">Phone</div>
  <div class="field" style="left:652px;top:248px">City</div>
  <div class="field" style="left:900px;top:248px">Zipcode</div>
  <div class="field message" style="left:652px;top:302px">Message</div>
  <div class="submit">SUBMIT NOW</div>
  <div class="abs cards"><span>Kredo</span><span>Amplo</span><span>Orbit</span><span>Duo</span><span>Paylo</span></div>
</section>

<footer class="section site-footer">
  <nav class="footer-nav"><span>ABOUT US</span><span>WHY US</span><span>OUR MASHROOMS</span><span>RECIEPE</span><span>REVIEWS</span><span>BLOGS</span><span>Q&amp;A</span><span>CONTACT</span></nav>
  <div class="copyright">© 2020 Company Name | All Rights Reserved | Disclaimer</div>
</footer>

</body>
</html>
```